Mortgage Company needs some fresh looking business cards to replace current outdated design

Looking for fresh ideas. The only requirement is that the card must show the following:Keelbrook Logo (uploaded)Keelbrook slogan "lending made simple"Equal Housing Lender logo (uploaded)Keelbrook NMLS #572081 (see current bus card, uploaded)Website as shown on sampleColor Codes as follows:Green = PMS 555 , #2b7051 , CMYK 83 33 77 21Rust = PMS 471 , #bc6225 , CMYK 21 70 100 8Would like two sided card. Front will have all of the above info, and back will have just the logo.

Target Market(s)

Consumers and Real Estate Agents

Industry/Entity Type

Mortgage Lender

Contact Information for Business Card

Color Codes as follows:
Green = PMS 555 , #2b7051 , CMYK 83 33 77 21
Rust = PMS 471 , #bc6225 , CMYK 21 70 100 8

Would like two sided card. Front will have all of the above info, and back will have just the logo.

Requirements
Must have
• Keelbrook Logo (uploaded)
• Keelbrook slogan "lending made simple"
• Equal Housing Lender logo (uploaded)
• Keelbrook NMLS #572081 (see current bus card, uploaded)
• Website as shown on sample

```html
<!DOCTYPE html>
<html lang="en">
<head>
<meta charset="utf-8">
<title>Keelbrook Mortgage – Business Cards</title>
<link rel="stylesheet" href="https://fonts.googleapis.com/css2?family=Playfair+Display:ital,wght@0,400;1,400&family=Open+Sans:wght@400;600&display=swap">
<style>
  :root {
    --green: #2b7051;
    --green-deep: #0f6a55;
    --rust: #bc6225;
    --rust-bright: #c96a1c;
    --paper: #ffffff;
    --backdrop: #c6c6c6;
    --photo-light: #d8d8d8;
    --photo-dark: #6f6f6f;
  }
  * { margin: 0; padding: 0; box-sizing: border-box; }
  html, body { width: 1200px; height: 900px; overflow: hidden; }
  body {
    background: var(--backdrop);
    font-family: "Open Sans", Arial, sans-serif;
    position: relative;
  }
  .card {
    position: absolute;
    width: 620px;
    height: 354px;
    background: var(--paper);
    overflow: hidden;
    box-shadow: 0 6px 18px rgba(0,0,0,0.18);
  }
  .card--back { left: 530px; top: 50px; }
  .card--front { left: 50px; top: 470px; }

  /* Company name */
  .brand { position: absolute; display: flex; align-items: center; gap: 10px; white-space: nowrap; }
  .brand__mark { width: 12px; height: 12px; background: var(--green); flex: none; }
  .brand__name {
    font-family: "Open Sans", Arial, sans-serif;
    font-weight: 600;
    color: var(--green);
    line-height: 1.2;
  }
  .tagline {
    position: absolute;
    font-family: "Open Sans", Arial, sans-serif;
    font-weight: 400;
    color: var(--rust);
    white-space: nowrap;
  }

  /* Back */
  .card--back .brand { left: 150px; top: 130px; }
  .card--back .brand__name { font-size: 32px; }
  .card--back .tagline { left: 172px; top: 180px; font-size: 16px; }
  .back__web {
    position: absolute; left: 172px; top: 238px;
    font-size: 14px; letter-spacing: 4px; color: var(--rust);
  }

  /* Front */
  .front__band-green {
    position: absolute; left: 0; top: 134px; width: 100%; height: 136px;
    background: linear-gradient(90deg, var(--green-deep), var(--green));
  }
  .front__band-rust {
    position: absolute; left: 0; top: 274px; width: 100%; height: 80px;
    background: var(--rust-bright);
  }
  .front__photo {
    position: absolute; left: 46px; top: 32px; width: 126px; height: 150px;
    border: 4px solid var(--paper);
    background: radial-gradient(circle at 50% 40%, var(--photo-light), var(--photo-dark));
  }
  .person { position: absolute; left: 46px; top: 192px; }
  .person__name {
    font-family: "Playfair Display", Georgia, serif;
    font-size: 20px; color: var(--paper); letter-spacing: 1px; line-height: 1.1;
  }
  .person__role, .person__nmls {
    font-family: "Playfair Display", Georgia, serif;
    font-size: 12px; color: var(--rust-bright); font-style: italic; line-height: 1.35;
  }
  .card--front .brand { left: 318px; top: 44px; }
  .card--front .brand__name { font-size: 23px; }
  .card--front .tagline { left: 340px; top: 80px; font-size: 13px; }

  .contact { position: absolute; left: 318px; top: 146px; list-style: none; }
  .contact li {
    display: flex; align-items: center; gap: 8px;
    color: var(--paper); font-size: 14px; line-height: 21px;
  }
  .contact svg { width: 13px; height: 13px; flex: none; }
  .contact .contact__plain { padding-left: 21px; }

  .apply {
    position: absolute; left: 120px; top: 288px;
    color: var(--paper); font-size: 15px; line-height: 21px; text-align: center;
  }
  .lender-badge {
    position: absolute; left: 534px; top: 292px; width: 42px; height: 42px;
    border: 3px solid var(--paper);
  }
</style>
</head>
<body>

  <section class="card card--back" aria-label="Card back">
    <div class="brand">
      <span class="brand__mark"></span>
      <span class="brand__name">Keelbrook Mortgage</span>
    </div>
    <div class="tagline">lending made simple</div>
    <div class="back__web">www.keelbrook.com</div>
  </section>

  <section class="card card--front" aria-label="Card front">
    <div class="front__band-green"></div>
    <div class="front__band-rust"></div>

    <div class="front__photo" role="img" aria-label="Portrait photo of the loan officer"></div>

    <div class="person">
      <div class="person__name">DALE PRESCOTT</div>
      <div class="person__role">Job Title</div>
      <div class="person__nmls">NMLS# 572081</div>
    </div>

    <div class="brand">
      <span class="brand__mark"></span>
      <span class="brand__name">Keelbrook Mortgage</span>
    </div>
    <div class="tagline">lending made simple</div>

    <ul class="contact">
      <li>
        <svg viewBox="0 0 16 16" aria-hidden="true"><path fill="#c96a1c" d="M2 5c0-2 2-3 6-3s6 1 6 3v1h-3V5H5v1H2zM3 7h10l1 7H2z"/><circle cx="8" cy="10.5" r="2" fill="#0f6a55"/></svg>
        000 000 0000
      </li>
      <li>
        <svg viewBox="0 0 16 16" aria-hidden="true"><rect x="4" y="1" width="8" height="14" rx="1.5" fill="none" stroke="#c96a1c" stroke-width="2"/><circle cx="8" cy="12" r="1" fill="#c96a1c"/></svg>
        000 000 0000
      </li>
      <li>
        <svg viewBox="0 0 16 16" aria-hidden="true"><rect x="1" y="3" width="14" height="10" fill="#c96a1c"/><path d="M1 3l7 6 7-6" fill="none" stroke="#0f6a55" stroke-width="1.3"/></svg>
        youremail@xyz.com
      </li>
      <li class="contact__plain">2180 Cedar Ridge Rd Ste 300</li>
      <li class="contact__plain">Austin, TX 78704</li>
    </ul>

    <div class="apply">Apply online at:<br>www.keelbrook.com</div>
    <div class="lender-badge" role="img" aria-label="Equal housing lender badge"></div>
  </section>

</body>
</html>
```